Need App for Impact Related Events

My app is to help with internal events. When you enter the prompted event code the next screen shows you everyone currently at the event. It will give you the ability to Start a conversation with someone you met at that event, or signal it is your turn to send a message. The next screen is a message thread with that person. I am looking for a design that incorporates the colors and ‘feel good’ emotion of our logo. I have pieced together a pretty good interpretation of what I’m looking for in the attached mockup by slicing and dicing designs. I also attached our logo mascot.Screens (see attached mockups)

Note 1: I do not like the picture on the screen used in screen one because it makes it seem like a dating app. I attached an alternative photo that can be used or present different ideas.

Note 2: On the login/signup screen (screen 2) I need an additional first and last name for login, you can try to fit this on one login screen or present a two step signup screen where that is presented in the second screen.

READ MOCKUP GUIDELINES UNDER Must Haves

Target Market(s)

People attending internal social impact events

Industry/Entity Type

Charity

Font styles to use
Sans Serif

Colors
86cfc6

Requirements
Must have
• Follow the screen mockups attached to project
• PLEASE READ
• I have provided a relatively close design of what I’m looking for in the mockups. Some screens need to be followed more closely to my design mockup than other. I have listed a guide below how how closely you should follow my mockup design exactly. Overall I would like to see some ideas of incorporating a few accent colors so it doesn’t appear SO Blue. I also attached some app inspiration designs I found from around the web
• Screen Mockup Guideline Follow %
• Screen 1: 65% - mostly on target, would like to see ways to make it not SO Blue and possibly creative places to add some explainer text describing the app
• Screen 2: 50% - general design idea is here, but more open
• Screen 3: 35% - a lot more room for design influence
• Screen 4: 70% - mostly on target, a little room for design influence/color scheme ideas
• Screen 5-6: 25% - a lot of room for design change/ideas/influence
• Screen 7-8: 80% - already very close to what I need, maybe open to slight sizing and color scheme ideas
• Screen 9: 15% - the most open for influence, only the general functionality of the screen is communicated here
Nice to have
• Please Read Mockup Guideline above. In large part I am looking for something to use some nice accent colors so it is not overwhelmingly blue and bring the whole design into a seamless style.
Should not have

```html
<!DOCTYPE html>
<html lang="en">
<head>
<meta charset="utf-8">
<title>Be Warm Be Open – Welcome</title>
<link rel="stylesheet" href="https://fonts.googleapis.com/css2?family=Mulish:wght@400;800&display=swap">
<style>
  :root {
    --bg: #ffffff;
    --ink: #23232f;
    --ink-soft: #2e2e38;
    --violet: #9452e6;
    --rose: #d98fbd;
    --mascot-a: #a86ae8;
    --mascot-b: #d49ad6;
    --on-accent: #ffffff;
  }
  * { box-sizing: border-box; margin: 0; padding: 0; }
  html, body {
    width: 675px;
    height: 1200px;
    overflow: hidden;
    background: var(--bg);
  }
  .welcome-screen {
    position: relative;
    width: 675px;
    height: 1200px;
    background: var(--bg);
    font-family: "Mulish", sans-serif;
    color: var(--ink);
  }
  .mascot {
    position: absolute;
    left: 180px;
    top: 255px;
    width: 290px;
    height: 240px;
    border-radius: 46% 54% 50% 50% / 55% 50% 50% 45%;
    background: linear-gradient(135deg, var(--mascot-a) 0%, var(--mascot-b) 100%);
  }
  .app-title {
    position: absolute;
    top: 598px;
    left: 0;
    width: 100%;
    text-align: center;
    font-size: 57px;
    font-weight: 800;
    letter-spacing: 0.5px;
    color: var(--ink);
  }
  .app-tagline {
    position: absolute;
    top: 728px;
    left: 100px;
    width: 475px;
    text-align: center;
    font-size: 32px;
    font-weight: 400;
    line-height: 43px;
    color: var(--ink-soft);
  }
  .continue-button {
    position: absolute;
    left: 150px;
    top: 1050px;
    width: 375px;
    height: 84px;
    border: none;
    border-radius: 4px;
    background: linear-gradient(90deg, var(--violet) 0%, var(--rose) 100%);
    color: var(--on-accent);
    font-family: "Mulish", sans-serif;
    font-size: 25px;
    font-weight: 400;
    letter-spacing: 2px;
    box-shadow: 0 4px 8px rgba(0, 0, 0, 0.18);
  }
</style>
</head>
<body>
  <main class="welcome-screen">
    <div class="mascot" role="img" aria-label="Friendly bee mascot illustration"></div>
    <h1 class="app-title">Be Warm Be Open</h1>
    <p class="app-tagline">A convenient way to Interact with strangers at gatherings.</p>
    <button class="continue-button" type="button">CONTINUE</button>
  </main>
</body>
</html>
```